Before the kettle boils, pocast with content in its majority of technology

Page dedicated to a pocast with content in its majority of technology. The page also contains the chapters of the podcast (pluggin vocalink) will also contain news. Preferably Worpress. There is already a very basic page with a simple theme, the logo and little more, I would like something more professional. Www.lamparadebolsillo.com The logo does not want to change.

Target Market(s)

Anyone

Colors

Designer to choose colors to be used in the design.

Requirements
Must have
• You can put the vocalink pluggin with the podcast chapters

```html
<!DOCTYPE html>
<html lang="en">
<head>
<meta charset="utf-8">
<title>Before the kettle boils – Podcast de Tecnologia</title>
<link href="https://fonts.googleapis.com/css2?family=Oswald:wght@400;500;600&family=Open+Sans:wght@400;600;700&display=swap" rel="stylesheet">
<style>
:root{
  --orange:#f07b1a;
  --orange-dark:#d9650c;
  --ink:#1b1b1b;
  --page:#151515;
  --panel:#222;
  --panel-line:#333;
  --white:#fff;
  --muted:#9a9a9a;
  --text:#555;
  --wave:#3a3a3a;
}
*{box-sizing:border-box;margin:0;padding:0}
html,body{width:1200px;height:3673px;overflow:hidden}
body{font-family:"Open Sans",Arial,sans-serif;background:var(--page);color:var(--white);position:relative}
.head-font{font-family:"Oswald",Arial,sans-serif;text-transform:uppercase}

/* hero */
.hero{position:absolute;left:0;top:0;width:1200px;height:558px;background:linear-gradient(100deg,#3a2a20 0%,#6b5444 35%,#8a7564 55%,#4a3a30 75%,#2a221d 100%)}
.hero-dancer{position:absolute;left:640px;top:0;width:420px;height:558px;background:radial-gradient(ellipse at 50% 45%,#b89a86 0%,#5a4338 45%,rgba(40,30,25,0) 75%)}
.hero-shade{position:absolute;inset:0;background:linear-gradient(90deg,rgba(0,0,0,.45),rgba(0,0,0,0) 60%)}
.brand{position:absolute;left:118px;top:22px;width:190px;text-align:center}
.brand-dot{width:62px;height:62px;border-radius:50%;background:var(--orange);margin:0 auto 6px}
.brand-name{font-family:"Oswald",sans-serif;font-size:15px;color:var(--orange);text-transform:uppercase;line-height:1.1}
.brand-sub{font-size:10px;color:#ddd;text-transform:uppercase;letter-spacing:.5px}
.nav{position:absolute;top:44px;left:340px;display:flex;align-items:center;gap:32px;font-family:"Oswald",sans-serif;font-size:15px;text-transform:uppercase}
.nav a{color:var(--white);text-decoration:none}
.nav a.active{color:var(--orange)}
.btn-login,.btn-signup{display:inline-flex;align-items:center;gap:6px;height:38px;padding:0 18px;border-radius:19px;font-size:14px}
.btn-login{border:2px solid var(--white);margin-left:4px}
.btn-signup{background:var(--orange);margin-left:-18px}
.hero-title{position:absolute;left:98px;top:218px;font-size:40px;font-weight:500;letter-spacing:.5px}
.hero-text{position:absolute;left:98px;top:286px;width:480px;font-size:16px;line-height:1.6;font-weight:600}
.hero-btn{position:absolute;left:98px;top:366px;width:170px;height:44px;border:2px solid var(--white);border-radius:22px;display:flex;align-items:center;justify-content:center;font-family:"Oswald",sans-serif;font-size:16px;text-transform:uppercase}
.dots{position:absolute;left:566px;top:488px;display:flex;gap:8px}
.dots span{width:12px;height:12px;border-radius:50%;border:2px solid var(--white)}
.dots span:first-child{background:var(--white)}

/* body backdrop */
.backdrop{position:absolute;left:0;top:558px;width:1200px;height:2883px;background:
 radial-gradient(ellipse 420px 700px at 1100px 2000px,rgba(240,123,26,.28),rgba(0,0,0,0) 70%),
 radial-gradient(ellipse 380px 600px at 80px 1900px,rgba(240,123,26,.22),rgba(0,0,0,0) 70%),
 radial-gradient(ellipse 500px 400px at 600px 1500px,rgba(80,60,40,.35),rgba(0,0,0,0) 70%),
 var(--page)}

/* main column */
.section-title{position:absolute;left:98px;top:624px;font-size:24px;font-weight:500}
.card{position:absolute;left:98px;width:624px;background:var(--white);color:var(--ink);padding:18px 20px}
.card-title{font-family:"Oswald",sans-serif;font-size:22px;font-weight:500;text-transform:uppercase;line-height:1.2}
.meta{display:flex;align-items:center;gap:10px;font-size:12px;color:#777;margin:10px 0 14px}
.meta .ico{color:var(--orange)}
.meta .sep{color:#ccc}
.stars{color:#f5b300;letter-spacing:1px}
.card-photo{width:584px;height:250px}
.player{margin-top:18px}
.player-label{display:flex;align-items:center;gap:8px;font-size:10px;text-transform:uppercase;color:#444}
.play{width:14px;height:14px;border-radius:50%;background:var(--orange);display:flex;align-items:center;justify-content:center}
.play::after{content:"";border-left:5px solid #fff;border-top:3px solid transparent;border-bottom:3px solid transparent;margin-left:1px}
.wave-row{display:flex;align-items:center;gap:8px;margin-top:6px}
.wave{width:560px;height:30px;background:repeating-linear-gradient(90deg,var(--wave) 0 2px,transparent 2px 3px);clip-path:polygon(0 30%,10% 15%,20% 35%,30% 10%,40% 30%,50% 20%,60% 35%,70% 15%,80% 25%,90% 10%,100% 30%,100% 80%,0 80%)}
.wave.played{background:linear-gradient(90deg,var(--orange) 0 78%,transparent 78%),repeating-linear-gradient(90deg,var(--wave) 0 2px,transparent 2px 3px)}
.wave-pill{width:22px;height:8px;border-radius:4px;background:#ccc}
.excerpt{font-size:12.5px;line-height:1.75;color:var(--text);margin-top:16px}
.card-foot{position:absolute;left:20px;right:20px;bottom:20px;display:flex;justify-content:space-between;align-items:center}
.read-more{width:124px;height:34px;border:1px solid #bbb;border-radius:17px;display:flex;align-items:center;justify-content:center;font-family:"Oswald",sans-serif;font-size:13px;color:var(--orange);text-transform:uppercase}
.shares{display:flex;gap:6px}
.share{display:flex;border:1px solid #ccc;border-radius:3px;font-size:11px;color:#333;height:22px;align-items:center}
.share b{padding:0 6px;font-weight:600;background:#f2f2f2;height:100%;display:flex;align-items:center;border-right:1px solid #ccc}
.share span{padding:0 6px}
.view-more{position:absolute;font-family:"Oswald",sans-serif;font-size:14px;color:var(--orange);text-transform:uppercase}

/* sidebar */
.side{position:absolute;left:754px;width:346px}
.ad-box{top:630px;height:264px;border:3px solid #ddd;background:linear-gradient(135deg,#3a2c28,#8a3a30 50%,#2a2020)}
.ad-label{position:absolute;left:0;right:0;top:116px;background:rgba(0,0,0,.45);padding:6px 8px}
.ad-label h3{font-family:"Oswald",sans-serif;font-size:24px;font-weight:500;text-transform:uppercase;border-bottom:2px solid #fff;padding-bottom:2px}
.ad-label p{font-family:"Oswald",sans-serif;font-size:16px;letter-spacing:2px;text-transform:uppercase;margin-top:2px}
.widget{background:var(--panel);border-top:3px solid var(--orange)}
.widget-head{position:absolute;top:-42px;left:0;height:42px;padding:0 32px 0 14px;background:var(--orange);font-family:"Oswald",sans-serif;font-size:20px;text-transform:uppercase;display:flex;align-items:center;clip-path:polygon(0 0,88% 0,100% 100%,0 100%)}
.post{display:flex;gap:14px;padding:12px 14px 8px}
.post-thumb{width:110px;height:80px;flex:none;border:2px solid #ddd}
.post-title{font-family:"Oswald",sans-serif;font-size:17px;line-height:1.3}
.post-meta{font-size:11px;color:#ccc;margin-top:6px}
.post-meta i{font-style:normal;color:var(--orange)}
.fan-box{margin:16px 14px 0;height:150px;background:#fff;color:#333;position:relative}
.fan-cover{height:150px;background:linear-gradient(120deg,#6b4a3a,#b08a6a 60%,#4a3a30)}
.fan-avatar{position:absolute;left:6px;top:8px;width:60px;height:60px;background:#2a2a2a;border:2px solid #fff}
.fan-name{position:absolute;left:74px;top:10px;font-size:13px;font-weight:700;color:#fff}
.fan-likes{position:absolute;left:74px;top:28px;font-size:11px;color:#eee}
.fan-btn{position:absolute;bottom:10px;height:26px;background:#f5f6f7;border:1px solid #ccc;font-size:12px;font-weight:600;display:flex;align-items:center;padding:0 10px}
.fan-note{font-size:11px;color:#ddd;margin:14px 14px 8px}
.fan-faces{display:flex;gap:6px;margin:0 14px}
.fan-faces span{width:40px;height:40px;background:#6a6058}
.nl-input{margin:22px 18px 0;height:44px;background:#fff;color:#666;font-size:11px;display:flex;align-items:center;padding:0 16px;text-transform:uppercase}
.nl-btn{margin:12px 18px 0;height:44px;border:2px solid #555;border-radius:22px;display:flex;align-items:center;justify-content:center;font-family:"Oswald",sans-serif;font-size:16px;color:var(--orange);text-transform:uppercase}
.nl-note{font-size:11px;line-height:1.6;color:#ddd;margin:16px 18px 0}
.poster{top:2356px;height:474px;border:3px solid #ddd;background:linear-gradient(180deg,#9fb0bd 0%,#d8c8a8 30%,#5a4a3a 60%,#1e1a18 100%)}

/* footer */
.footer{position:absolute;left:0;top:3441px;width:1200px;height:232px;background:#0e0e0e;border-top:3px solid var(--orange)}
.contacts{position:absolute;top:36px;left:196px;display:flex;font-size:14px;line-height:1.6}
.contact{display:flex;align-items:center;gap:18px;width:270px}
.contact:nth-child(2){width:210px}
.c-ico{width:42px;height:42px;border-radius:50%;background:#fff;display:flex;align-items:center;justify-content:center;flex:none}
.foot-links{position:absolute;top:114px;left:0;width:1200px;text-align:center;font-size:14px;color:#eee}
.foot-links span{color:#888;margin:0 8px}
.foot-line{position:absolute;top:150px;left:98px;width:1004px;height:1px;background:#2a2a2a}
.copyright{position:absolute;top:184px;left:98px;font-size:13px;color:#ddd}
.socials{position:absolute;top:174px;right:98px;display:flex;gap:8px}
.socials span{width:32px;height:32px;border-radius:50%;border:2px solid #ddd}
</style>
</head>
<body>

<header class="hero">
  <div class="hero-dancer" role="img" aria-label="Photo of a woman dancing with headphones"></div>
  <div class="hero-shade"></div>
  <div class="brand">
    <div class="brand-dot"></div>
    <div class="brand-name">Before the kettle boils</div>
    <div class="brand-sub">Podcast de tecnologia</div>
  </div>
  <nav class="nav">
    <a class="active">Home</a><a>Podcasts</a><a>Features</a><a>Pricing</a><a>Program</a><a>Contact</a>
    <svg width="16" height="16" viewBox="0 0 16 16"><circle cx="6.5" cy="6.5" r="5" fill="none" stroke="#fff" stroke-width="2"/><line x1="10" y1="10" x2="15" y2="15" stroke="#fff" stroke-width="2"/></svg>
    <span class="btn-login">
      <svg width="11" height="13" viewBox="0 0 11 13"><rect x="0" y="5" width="11" height="8" fill="#fff"/><path d="M2.5 5V3.5a3 3 0 0 1 6 0V5" fill="none" stroke="#fff" stroke-width="1.6"/></svg>Login</span>
    <span class="btn-signup">
      <svg width="12" height="12" viewBox="0 0 12 12"><path d="M1 11l1-3 7-7 2 2-7 7z" fill="#fff"/></svg>Sign up</span>
  </nav>
  <h1 class="hero-title head-font">Podcast de Techologia</h1>
  <p class="hero-text">Nam libero tempore, cum soluta nobis est eligendi otio cumque nihil impedit quo minus.</p>
  <div class="hero-btn">Start now!</div>
  <div class="dots"><span></span><span></span><span></span><span></span></div>
</header>

<div class="backdrop" role="img" aria-label="Blurred photo of a DJ at a console in warm orange light"></div>

<main>
  <h2 class="section-title head-font">Latest Podcast</h2>

  <article class="card" style="top:688px;height:647px">
    <h3 class="card-title">Cambio de logo</h3>
    <div class="meta"><span class="ico">▦</span>19 May, 2017<span class="sep">|</span><span class="ico">●</span>de lucerno<span class="sep">|</span><span class="stars">★★★★☆</span>(34 Reviews)</div>
    <div class="card-photo" style="background:linear-gradient(180deg,#f6d27a 0%,#f3a43a 45%,#c06a1a 75%,#5a3a1a 100%)" role="img" aria-label="Photo of a person raising arms toward a sunset"></div>
    <div class="player">
      <div class="player-label"><span class="play"></span>Change logo</div>
      <div class="wave-row"><div class="wave played"></div><div class="wave-pill"></div></div>
    </div>
    <p class="excerpt">Hello to Tod @ s!<br>Is it obvious, then? We renew the design of the logo and something on the web. Here the changes will go little by little but I will try to leave everything that I want to modify done in a week at most, everything will depend on the time that I can dedicate to him although the difficult thing is already done.</p>
    <div class="card-foot"><div class="read-more">Read more &gt;&gt;</div>
      <div class="shares"><div class="share"><b>Like</b><span>200</span></div><div class="share"><b>Post</b><span>200</span></div><div class="share"><b>+1</b><span>200</span></div></div></div>
  </article>

  <article class="card" style="top:1357px;height:646px">
    <h3 class="card-title">Do you like series? Do you know serielab.tv?</h3>
    <div class="meta"><span class="ico">▦</span>17 May, 2017<span class="sep">|</span><span class="ico">●</span>de lucerno<span class="sep">|</span><span class="stars">★★★★☆</span>(34 Reviews)</div>
    <div class="card-photo" style="background:linear-gradient(90deg,#9a6a3a,#c08a52 40%,#6a4a2a 70%,#b07a44)" role="img" aria-label="Photo of yellow headphones and a smartphone on a wooden table"></div>
    <div class="player">
      <div class="player-label"><span class="play"></span>Do you like series? Do you know serielab.tv?</div>
      <div class="wave-row"><div class="wave"></div><div class="wave-pill"></div></div>
    </div>
    <p class="excerpt">Hello everyone!<br>Today chapter dedicated to the lovers of the series and the films. It is the streaming video service of the website serielab.tv portal dedicated to learning English through the method of watching movies and series in English with subtitles.</p>
    <div class="card-foot"><div class="read-more">Read more &gt;&gt;</div>
      <div class="shares"><div class="share"><b>Like</b><span>200</span></div><div class="share"><b>Post</b><span>200</span></div><div class="share"><b>+1</b><span>200</span></div></div></div>
  </article>

  <article class="card" style="top:2025px;height:645px">
    <h3 class="card-title">An advertisement and a test</h3>
    <div class="meta"><span class="ico">▦</span>May 13, 2017<span class="sep">|</span><span class="ico">●</span>de lucerno<span class="sep">|</span><span class="stars">★★★★☆</span>(34 Reviews)</div>
    <div class="card-photo" style="background:linear-gradient(110deg,#3a2a40,#8a6a7a 40%,#c4a090 60%,#4a3040)" role="img" aria-label="Photo of a laughing woman wearing headphones"></div>
    <div class="player">
      <div class="player-label"><span class="play"></span>An advertisement and a test</div>
      <div class="wave-row"><div class="wave"></div><div class="wave-pill"></div></div>
    </div>
    <p class="excerpt">Hello everyone!<br>Yes, I know it has happened again, a long time since the last publication. This I have very abandoned and there is no excuse, I feel sorry but it is true, for ganduleria or for reasons of time I have not dedicated the attention that deserves.</p>
    <div class="card-foot"><div class="read-more">Read more &gt;&gt;</div>
      <div class="shares"><div class="share"><b>Like</b><span>200</span></div><div class="share"><b>Post</b><span>200</span></div><div class="share"><b>+1</b><span>200</span></div></div></div>
  </article>

  <article class="card" style="top:2694px;height:624px">
    <h3 class="card-title">Security in your mail</h3>
    <div class="meta"><span class="ico">▦</span>Nov 23, 2016<span class="sep">|</span><span class="ico">●</span>de lucerno<span class="sep">|</span><span class="stars">★★★★☆</span>(34 Reviews)</div>
    <div class="card-photo" style="background:linear-gradient(120deg,#2a2a2a,#6a6a6a 45%,#bcbcbc 60%,#3a3a3a)" role="img" aria-label="Black and white photo of studio headphones"></div>
    <div class="player">
      <div class="player-label"><span class="play"></span>Security in your mail</div>
      <div class="wave-row"><div class="wave"></div><div class="wave-pill"></div></div>
    </div>
    <p class="excerpt">Hello everyone!<br>Today little more to say about here said in the podcast. For those who need an extra point of security in the email is CofreMail. Free and paid plans, coding, messages that can be destroyed, etc.</p>
    <div class="card-foot"><div class="read-more">Read more &gt;&gt;</div>
      <div class="shares"><div class="share"><b>Like</b><span>200</span></div><div class="share"><b>Post</b><span>200</span></div><div class="share"><b>+1</b><span>200</span></div></div></div>
  </article>

  <div class="view-more" style="left:98px;top:3354px">View more &gt;&gt;</div>
</main>

<aside>
  <div class="side ad-box" role="img" aria-label="Photo of a microphone and headphones for podcast advertising">
    <div class="ad-label"><h3>Podcast advertising</h3><p>What you need to know</p></div>
  </div>

  <section class="side widget" style="top:980px;height:612px">
    <div class="widget-head">Recent posts</div>
    <div class="post"><div class="post-thumb" style="background:#5a5a5a" role="img" aria-label="Thumbnail of a smartphone"></div><div><div class="post-title">Un anuncio y una prueba</div><div class="post-meta"><i>▦</i> 13 May, 2017 &nbsp;<i>●</i> lucerno</div></div></div>
    <div class="post"><div class="post-thumb" style="background:#6a8a90" role="img" aria-label="Thumbnail of a series banner"></div><div><div class="post-title">¿Te gustan las series?¿Conoces serielab.tv?</div><div class="post-meta"><i>▦</i> 13 May, 2017 &nbsp;<i>●</i> lucerno</div></div></div>
    <div class="post"><div class="post-thumb" style="background:#9aa0a0" role="img" aria-label="Thumbnail of earphones"></div><div><div class="post-title">Seguridad en tu Mail</div><div class="post-meta"><i>▦</i> 13 May, 2017 &nbsp;<i>●</i> lucerno</div></div></div>
    <div class="post"><div class="post-thumb" style="background:#7a6a60" role="img" aria-label="Thumbnail of a tablet"></div><div><div class="post-title">Tablon Pad2, calidad precio insuperable</div><div class="post-meta"><i>▦</i> 13 May, 2017 &nbsp;<i>●</i> lucerno</div></div></div>
    <div class="post"><div class="post-thumb" style="background:#8a7060" role="img" aria-label="Thumbnail of a person listening"></div><div><div class="post-title">Tertulia Frutaliana : Servicios en la nube</div><div class="post-meta"><i>▦</i> 13 May, 2017 &nbsp;<i>●</i> lucerno</div></div></div>
    <div class="view-more" style="left:14px;bottom:16px;font-size:13px">View more &gt;&gt;</div>
  </section>

  <section class="side widget" style="top:1666px;height:292px">
    <div class="widget-head">Join our fan page</div>
    <div class="fan-box">
      <div class="fan-cover" role="img" aria-label="Cover photo of the fan page"></div>
      <div class="fan-avatar"></div>
      <div class="fan-name">Before the kettle boils</div>
      <div class="fan-likes">4,691 followers</div>
      <div class="fan-btn" style="left:6px">Follow</div>
      <div class="fan-btn" style="right:6px">Sign Up</div>
    </div>
    <p class="fan-note">Be the first of your friends to follow this</p>
    <div class="fan-faces"><span></span><span></span><span></span><span></span><span></span><span></span><span></span></div>
  </section>

  <section class="side widget" style="top:2064px;height:252px">
    <div class="widget-head">Newsletter sign up</div>
    <div class="nl-input">Enter your email address</div>
    <div class="nl-btn">Sign up</div>
    <p class="nl-note">By signing up, you are opting in to receive periodic communications from Before the kettle boils</p>
  </section>

  <div class="side poster" role="img" aria-label="Movie poster showing a rear-view mirror over a lone figure on a desert road"></div>
</aside>

<footer class="footer">
  <div class="contacts">
    <div class="contact"><span class="c-ico"><svg width="16" height="20" viewBox="0 0 16 20"><path d="M8 0a8 8 0 0 1 8 8c0 6-8 12-8 12S0 14 0 8a8 8 0 0 1 8-8z" fill="#111"/><circle cx="8" cy="8" r="3" fill="#fff"/></svg></span><span>212 Harbor Lane, 4th Floor<br>Portside, NY 10099</span></div>
    <div class="contact"><span class="c-ico"><svg width="18" height="18" viewBox="0 0 18 18"><path d="M4 1l3 4-2 2c1 3 3 5 6 6l2-2 4 3-2 3C7 17 1 11 1 3z" fill="#111"/></svg></span><span>+1 555 010 2040</span></div>
    <div class="contact"><span class="c-ico"><svg width="18" height="14" viewBox="0 0 18 14"><rect width="18" height="14" fill="#111"/><path d="M1 1l8 7 8-7" fill="none" stroke="#fff" stroke-width="1.5"/></svg></span><span>info@lamparadebolsillo.com/</span></div>
  </div>
  <div class="foot-links">Home<span>|</span>Podcasts<span>|</span>Features<span>|</span>Pricing<span>|</span>Program<span>|</span>Contact</div>
  <div class="foot-line"></div>
  <div class="copyright">Copyrights © 2017, Before the kettle boils . All rights reserved.</div>
  <div class="socials"><span></span><span></span><span></span><span></span></div>
</footer>

</body>
</html>
```